Business card design for holistic health care clinic

We need a double-sided business card design for our holistic health care clinic that integrates our logo design and also its color scheme. My business is called Valmira. It is an integrative medicine clinic. You have already done the logo for me. Please ensure an elegant and upscale design that is not cluttered, but still has all the necessary information (please see below for details).

Target Market(s)

Wellness, fitness, rehabilitation for educated, well-traveled open-minded clients who are focused on natural, organic, balanced and preventive healthcare and lifestyle.

Industry/Entity Type

Medical

Contact Information for Business Card

Modern, clean.

Number of Pages Required

1 page

Font styles to use
Serif
Sans Serif

Colors

Designer to choose colors to be used in the design.

Requirements
Must have
• Logo on one side, all other information on the other side.
• Other information should include:
• Tobias Wrenfeld - DOE, CPT, LMT
• 4100 East Marrow Drive
• Austin, TX 78119
• 512 555 0148
• 818 555 0192
• info@ValmiraHealth.example
• t.wrenfeld@ValmiraHealth.example
Nice to have
• Darker background on front - but not totally black - shaded/dark gray.

```html
<!DOCTYPE html>
<html lang="en">
<head>
<meta charset="utf-8">
<title>Valmira – Business Card</title>
<link href="https://fonts.googleapis.com/css2?family=Work+Sans:wght@400;500;600&display=swap" rel="stylesheet">
<style>
  :root {
    --page-bg: #161616;
    --card-dark: #262626;
    --card-mid: #313131;
    --brand-blue: #1b9ad8;
    --text-light: #f2f2f2;
    --silver: #bdbdbd;
    --silver-dark: #5a5a5a;
  }
  * { box-sizing: border-box; margin: 0; padding: 0; }
  html, body {
    width: 1200px; height: 900px; overflow: hidden;
    background: var(--page-bg);
    font-family: "Work Sans", Arial, sans-serif;
  }
  .canvas {
    position: relative; width: 1200px; height: 900px;
    display: flex; flex-direction: column; align-items: center;
    justify-content: center; gap: 40px;
  }
  .card {
    position: relative; width: 700px; height: 400px; overflow: hidden;
    background: linear-gradient(135deg, var(--card-dark) 0%, var(--card-mid) 60%, var(--card-dark) 100%);
  }
  /* Front */
  .card-front {
    display: flex; flex-direction: column; align-items: center; justify-content: center;
  }
  .front-brand {
    display: flex; flex-direction: column; align-items: center;
    margin-top: 10px;
  }
  .brand-name {
    font-weight: 600; letter-spacing: 2px; line-height: 1;
    text-transform: uppercase;
  }
  .front-brand .brand-name { font-size: 92px; color: var(--silver); }
  .front-brand .brand-tagline {
    font-size: 24px; font-weight: 500; letter-spacing: 1.5px;
    color: var(--silver-dark); margin-top: 10px;
  }
  .front-web {
    position: absolute; bottom: 52px; left: 0; right: 0; text-align: center;
    font-size: 17px; letter-spacing: 2px; color: var(--text-light);
  }
  .accent { color: var(--brand-blue); }
  /* Back */
  .card-back { display: flex; align-items: center; padding: 0 20px 0 40px; }
  .back-brand { flex: none; width: 270px; display: flex; flex-direction: column; }
  .back-brand .brand-name { font-size: 60px; color: var(--brand-blue); }
  .back-brand .brand-tagline {
    font-size: 16px; font-weight: 600; color: var(--brand-blue);
    margin-top: 8px; letter-spacing: 0.3px;
  }
  .divider {
    flex: none; width: 3px; height: 240px; background: var(--brand-blue);
    margin: 0 24px;
  }
  .contact { flex: 1; min-width: 0; color: var(--text-light); }
  .person-name {
    font-size: 24px; font-weight: 500; letter-spacing: 2.5px;
    color: var(--brand-blue); text-transform: uppercase; white-space: nowrap;
  }
  .credentials { font-size: 15px; letter-spacing: 1px; margin-top: 2px; }
  .address { font-size: 15px; letter-spacing: 0.6px; margin-top: 12px; line-height: 1.3; }
  .lines { list-style: none; margin-top: 10px; }
  .lines li {
    display: flex; align-items: center; gap: 9px; white-space: nowrap;
    font-size: 15px; letter-spacing: 0.3px; line-height: 1.6;
  }
  .lines svg { width: 14px; height: 14px; flex: none; fill: var(--brand-blue); }
</style>
</head>
<body>
<main class="canvas">
  <section class="card card-front" aria-label="Card front">
    <div class="front-brand">
      <span class="brand-name">Valmira</span>
      <span class="brand-tagline">Integrative Holistic Medicine</span>
    </div>
    <p class="front-web">www.<span class="accent">valmirahealth</span>.example</p>
  </section>

  <section class="card card-back" aria-label="Card back">
    <div class="back-brand">
      <span class="brand-name">Valmira</span>
      <span class="brand-tagline">Integrative Holistic Medicine</span>
    </div>
    <div class="divider"></div>
    <div class="contact">
      <h1 class="person-name">Tobias Wrenfeld</h1>
      <p class="credentials">DOE, CPT, LMT</p>
      <p class="address">4100 East Marrow Drive<br>Austin, TX 78119</p>
      <ul class="lines">
        <li><svg viewBox="0 0 16 16"><path d="M3.6 1.2l2.3 2.6-1.2 1.9c.9 2 2.4 3.5 4.4 4.5l1.9-1.2 2.6 2.3-1.3 2.6C7.1 13.6 2.4 8.9 1 3.2z"/></svg><span>512 555 0148</span></li>
        <li><svg viewBox="0 0 16 16"><path d="M4.5 1h7v14h-7zM6 2.5v9.5h4V2.5zM7.3 13h1.4v1H7.3z" fill-rule="evenodd"/></svg><span>818 555 0192</span></li>
        <li><svg viewBox="0 0 16 16"><path d="M1 3.5h14v9H1zM2.2 4.5L8 9l5.8-4.5z" fill-rule="evenodd"/></svg><span>info@ValmiraHealth.example</span></li>
        <li><svg viewBox="0 0 16 16"><path d="M1 3.5h14v9H1zM2.2 4.5L8 9l5.8-4.5z" fill-rule="evenodd"/></svg><span>t.wrenfeld@ValmiraHealth.example</span></li>
        <li class="web"><svg viewBox="0 0 16 16"><path d="M8 1a7 7 0 1 0 0 14A7 7 0 0 0 8 1zm0 1.3c.9.8 1.6 2.5 1.8 4.7H6.2C6.4 4.8 7.1 3.1 8 2.3zM2.4 7h2.6c.1-1.7.5-3.2 1.1-4.2A5.7 5.7 0 0 0 2.4 7zm0 2a5.7 5.7 0 0 0 3.7 4.2C5.5 12.2 5.1 10.7 5 9zm3.8 0h3.6C9.6 11.2 8.9 12.9 8 13.7 7.1 12.9 6.4 11.2 6.2 9zm4.8 0h2.6a5.7 5.7 0 0 1-3.7 4.2c.6-1 1-2.5 1.1-4.2zm2.6-2H11c-.1-1.7-.5-3.2-1.1-4.2A5.7 5.7 0 0 1 13.6 7z"/></svg><span>www.<span class="accent">valmirahealth</span>.example</span></li>
      </ul>
    </div>
  </section>
</main>
</body>
</html>
```